Steadfast Field Crews

We are a underground coal mining labour hire company, needing a website that links into our online payroll (www.wagelinkr.com.au) and also need to have job applications page that is a preform with drop down menu,s with answers or check boxes. We would also need a 3 tier administration access for access to different files.
We are looking for an ongoing relationship with future app integration

Reason: There are a few more designs to come and I'm out at the mine for another week

Industry/Entity Type

Coal Mining

```html
<!DOCTYPE html>
<html lang="en">
<head>
<meta charset="utf-8">
<title>Steadfast Field Crews</title>
<link href="https://fonts.googleapis.com/css2?family=Open+Sans:wght@300;400;600&family=Arimo:wght@400;700&family=Questrial&display=swap" rel="stylesheet">
<style>
:root{
  --orange:#f0801f;
  --orange-dark:#d8650e;
  --orange-deep:#b94f07;
  --ink:#1a1a1a;
  --charcoal:#262626;
  --panel:#3a3a3a;
  --panel-line:#555;
  --text-light:#e6e6e6;
  --text-muted:#c9c9c9;
  --white:#fff;
  --yellow:#f8b81a;
  --red:#b8342a;
}
*{box-sizing:border-box;margin:0;padding:0}
html,body{width:908px;height:1200px;overflow:hidden}
body{position:relative;font-family:"Arimo",Arial,sans-serif;background:linear-gradient(180deg,#3b3b3b 0%,#4a4a4a 40%,#3d3d3d 70%,#555 100%);color:var(--text-light)}
.abs{position:absolute}
.site-header{left:0;top:0;width:908px;height:84px;background:linear-gradient(180deg,#0d0d0d,#1f1f1f)}
.brand{left:120px;top:8px;display:flex;align-items:center;gap:14px}
.brand-mark{width:70px;height:70px;border-radius:50%;background:var(--orange)}
.brand-name{font-family:"Questrial",Arial,sans-serif;font-size:25px;line-height:30px;color:var(--white);letter-spacing:.5px;text-transform:uppercase}
.account-box{left:651px;top:0;width:142px;height:43px;background:var(--orange);border-radius:0 0 8px 8px;font-size:10px;color:var(--white)}
.account-links{display:flex;justify-content:space-around;padding-top:4px}
.socials{display:flex;gap:5px;justify-content:center;margin-top:5px}
.socials span{width:14px;height:14px;border-radius:50%;background:var(--white);display:block}
.hotline{left:657px;top:54px;font-size:16px;font-weight:700;color:var(--orange);display:flex;align-items:center;gap:8px}
.main-nav{left:0;top:84px;width:908px;height:36px;background:var(--orange)}
.main-nav ul{list-style:none;display:flex;margin-left:113px;height:36px}
.main-nav li{font-size:8.5px;color:var(--white);text-transform:uppercase;padding:0 14px;line-height:36px;border-right:1px solid rgba(255,255,255,.25)}
.main-nav li.current{background:#f6a35a}
.hero{left:0;top:127px;width:908px;height:262px;background:linear-gradient(100deg,#6b4e2e 0%,#a8793f 30%,#3a2a1a 55%,#2d2d2d 75%,#7a6a55 100%)}
.hero-arrow{top:110px;width:22px;height:22px;border-radius:50%;background:#111}
.hero-caption{left:14px;top:309px;font-family:"Questrial",Arial,sans-serif;font-size:28px;line-height:37px;text-transform:uppercase}
.hero-caption .l1{color:var(--white);font-size:25px}
.hero-caption .l2{color:var(--ink);background:rgba(255,255,255,.35);padding-right:6px}
.service-card{top:411px;width:158px;height:209px;background:var(--white);border:3px solid #555}
.service-card .photo{height:83px}
.service-card h3{font-family:"Questrial",Arial,sans-serif;font-weight:400;font-size:15px;color:var(--orange);margin:10px 0 4px 4px;text-transform:uppercase}
.service-card p{font-size:8px;line-height:10px;color:var(--ink);padding:0 6px}
.btn{position:absolute;left:6px;bottom:9px;width:80px;height:22px;border-radius:4px;font-size:10px;color:var(--white);text-align:center;line-height:22px}
.btn-orange{background:var(--orange)}
.btn-dark{background:var(--ink)}
.side-promos{left:619px;top:411px;width:174px;height:209px;background:#fff;border:3px solid #555}
.vacancy{height:78px;background:linear-gradient(90deg,#c68a4a,var(--orange-dark));position:relative}
.vacancy h4{position:absolute;left:74px;top:10px;font-family:"Questrial",Arial,sans-serif;font-weight:400;color:var(--white);font-size:15px;line-height:18px}
.vacancy .apply{position:absolute;left:72px;top:55px;background:#3a3a3a;color:#fff;font-size:8px;padding:3px 12px;border-radius:3px}
.promo{position:absolute;left:3px;width:163px;height:46px;display:flex}
.promo .icon{width:48px;background:var(--ink);display:flex;align-items:center;justify-content:center}
.promo .label{flex:1;background:var(--yellow);font-size:11px;font-weight:700;line-height:13px;padding:4px 0 0 8px;text-transform:uppercase;color:var(--white)}
.welcome{left:115px;top:635px;width:680px;height:202px;background:rgba(55,55,55,.92)}
.welcome h1{position:absolute;left:6px;top:4px;font-family:"Open Sans",Arial,sans-serif;font-weight:300;font-size:30px;color:#ddd}
.welcome .photo{position:absolute;left:4px;top:50px;width:173px;height:144px;border:3px solid #777;background:linear-gradient(160deg,#6a6a6a,#2b2b2b)}
.welcome .copy{position:absolute;left:189px;top:42px;width:484px;font-size:7.6px;line-height:11.6px;color:var(--text-muted)}
.welcome .copy p+p{margin-top:12px}
.news{left:115px;top:853px;width:315px;height:180px}
.section-title{font-family:"Questrial",Arial,sans-serif;font-size:15px;color:var(--text-light);text-transform:uppercase;border-bottom:1px solid var(--panel-line);padding:3px 8px 5px}
.news-item{display:flex;gap:8px;padding:9px 6px 8px 6px;border-bottom:1px solid var(--panel-line)}
.date{width:49px;height:48px;background:var(--orange);color:var(--white);text-align:center;font-family:"Questrial",Arial,sans-serif;flex-shrink:0}
.date b{display:block;font-size:22px;font-weight:400;line-height:26px;border-bottom:1px solid rgba(255,255,255,.5)}
.date i{font-style:normal;font-size:16px;line-height:20px}
.news-item p{font-size:8px;line-height:11px;color:var(--text-muted)}
.news-item .more{color:var(--orange);text-decoration:underline}
.testimonials{left:455px;top:853px;width:338px;height:180px}
.testi-box{margin:10px 4px 0 4px;height:137px;background:#4a4a4a;border:1px solid #5c5c5c;position:relative}
.testi-box .photo{position:absolute;left:4px;top:8px;width:72px;height:70px;border:2px solid #888;background:linear-gradient(150deg,#e2a040,#6a5a44)}
.testi-box h5{position:absolute;left:88px;top:10px;font-weight:400;font-size:11px;color:var(--white)}
.testi-box .quote{position:absolute;left:95px;top:36px;width:232px;font-size:8px;line-height:11px;color:var(--text-muted)}
.testi-box .more{position:absolute;left:100px;top:119px;font-size:8px;color:var(--orange)}
.site-footer{left:0;top:1047px;width:908px;height:124px;background:linear-gradient(180deg,var(--orange-dark),var(--orange))}
.foot-col{position:absolute;top:12px}
.foot-col h6{font-family:"Questrial",Arial,sans-serif;font-weight:400;font-size:13px;color:var(--ink);margin-bottom:6px}
.foot-col ul{list-style:none}
.foot-col li{font-size:8.5px;line-height:14px;color:var(--white)}
.foot-col li::before{content:"›";margin-right:6px}
.foot-col p{font-size:8.5px;line-height:12px;color:var(--white)}
.divider{position:absolute;top:12px;width:1px;height:98px;background:rgba(0,0,0,.25)}
.email-field{display:flex;margin-top:4px}
.email-field span{width:94px;height:16px;background:#fff}
.email-field b{width:16px;height:16px;background:var(--ink)}
.contact-card{left:660px;top:16px;width:135px;height:103px;background:#141414;border-radius:4px;font-size:8.5px;color:var(--white);padding:9px 10px}
.contact-row{display:flex;gap:8px;margin-bottom:8px;line-height:11px}
.copyright{left:0;top:1171px;width:908px;height:29px;background:var(--orange-deep);text-align:center;font-size:7.5px;color:var(--white);line-height:29px}
</style>
</head>
<body>

<header class="site-header abs">
  <div class="brand abs">
    <span class="brand-mark"></span>
    <span class="brand-name">Steadfast<br>Field Crews</span>
  </div>
</header>

<div class="account-box abs">
  <div class="account-links"><span>Sign up</span><span>Login</span></div>
  <div class="socials" aria-label="Social links"><span></span><span></span><span></span></div>
</div>
<div class="hotline abs">
  <svg width="14" height="12" viewBox="0 0 14 12"><path d="M1 4c0-2 3-3 6-3s6 1 6 3l-2 1-1-2H4L3 5z M3 6h8l1 5H2z" fill="#fff"/></svg>
  <span>1800 555 014</span>
</div>

<nav class="main-nav abs">
  <ul>
    <li class="current">Home</li><li>About Us</li><li>Capabilities</li><li>Job Seekers</li><li>Equipment Hire</li><li>Labour Hire</li><li>Harlow Engineering</li><li>Projects</li><li>CMS Training</li>
  </ul>
</nav>

<section class="hero abs" role="img" aria-label="Miners working in an underground coal mine tunnel with lit headlamps"></section>
<span class="hero-arrow abs" style="left:4px;top:237px"></span>
<span class="hero-arrow abs" style="left:880px;top:237px"></span>
<div class="hero-caption abs">
  <div class="l1">Ground Consolidation and</div>
  <div class="l2">Underground Coal Mines</div>
</div>

<article class="service-card abs" style="left:115px">
  <div class="photo" role="img" aria-label="Miner in hi-vis gear in a lit tunnel" style="background:linear-gradient(135deg,#c98a3a,#3a2816)"></div>
  <h3>Underground</h3>
  <p>Skilled crews for deep shafts and long shifts, inducted, certified and ready to mobilise to your site.</p>
  <span class="btn btn-orange">Read More</span>
</article>
<article class="service-card abs" style="left:283px">
  <div class="photo" role="img" aria-label="Earthmoving machinery on a construction site" style="background:linear-gradient(180deg,#8fa4b8,#9a8a66 60%,#6b5a3e)"></div>
  <h3>Construction</h3>
  <p>Operators and labourers for civil works, haul roads and site preparation, supplied on short notice.</p>
  <span class="btn btn-dark">Read More</span>
</article>
<article class="service-card abs" style="left:451px">
  <div class="photo" role="img" aria-label="Haul truck loading coal at an open cut mine" style="background:linear-gradient(180deg,#7d97b3,#6a6a6a 55%,#2a2a2a)"></div>
  <h3>Mining</h3>
  <p>Experienced miners, fitters and electricians for open cut and underground coal operations across the state.</p>
  <span class="btn btn-dark">Read More</span>
</article>

<aside class="side-promos abs">
  <div class="vacancy">
    <div role="img" aria-label="Smiling worker in a hard hat" style="position:absolute;left:0;top:0;width:66px;height:78px;background:linear-gradient(180deg,#e8e0d4,#e58a2e)"></div>
    <h4>JOB<br>VACANCY</h4>
    <span class="apply">APPLY NOW</span>
  </div>
  <div class="promo" style="top:88px">
    <span class="icon"><svg width="28" height="18" viewBox="0 0 28 18"><path d="M2 9l6-6 6 4 6-4 6 6-8 7-4-3-4 3z" fill="#fff"/></svg></span>
    <span class="label">View<br>Employee<br>Benefits</span>
  </div>
  <div class="promo" style="top:150px">
    <span class="icon" style="background:var(--red)"><svg width="24" height="18" viewBox="0 0 24 18"><circle cx="7" cy="5" r="3.5" fill="#fff"/><circle cx="17" cy="5" r="3.5" fill="#fff"/><path d="M1 17c0-5 12-5 12 0zM11 17c0-5 12-5 12 0z" fill="#fff"/></svg></span>
    <span class="label" style="font-size:12px;line-height:15px;padding-top:8px">Labor Hire<br>Click Here</span>
  </div>
</aside>

<section class="welcome abs">
  <h1>Welcome to our site</h1>
  <div class="photo" role="img" aria-label="Workers shovelling coal"></div>
  <div class="copy">
    <p>Steadfast Field Crews supplies experienced labour to underground coal mines and surface projects. Our people arrive inducted, fit for work and backed by a team that answers the phone at any hour. We place miners, deputies, fitters, electricians and general labourers on short and long term assignments, and we manage rosters, tickets and pay so site managers can focus on production. Every worker completes our safety induction before starting, and our supervisors visit each site regularly to check that crews are settled, safe and productive. Whether you need one operator for a weekend shutdown or a full crew for a new development panel, we can help.</p>
    <p>Job seekers can apply online in minutes and track their application, while current crew members log in to view rosters and payslips through our payroll portal. We look forward to building long term partnerships with mine operators and contractors.</p>
  </div>
</section>

<section class="news abs">
  <h2 class="section-title">Recent News</h2>
  <div class="news-item">
    <div class="date"><b>15</b><i>mar</i></div>
    <p>New crews mobilised to the northern coal fields this month. Inductions are complete and all teams are on site and working safely. <span class="more">Read More</span></p>
  </div>
  <div class="news-item">
    <div class="date"><b>16</b><i>mar</i></div>
    <p>Applications are open for experienced underground fitters and electricians. Submit your details through the job seekers page today. <span class="more">Read More</span></p>
  </div>
</section>

<section class="testimonials abs">
  <h2 class="section-title">Testimonials</h2>
  <div class="testi-box">
    <div class="photo" role="img" aria-label="Mining excavator on site"></div>
    <h5>Dana Whitcombe</h5>
    <p class="quote">“ Steadfast found us a full development crew within a week. Their people were inducted, capable and safety focused from the first shift, and the paperwork was simple. ”</p>
    <span class="more">MORE ›</span>
  </div>
</section>

<footer class="site-footer abs">
  <div class="foot-col" style="left:116px">
    <h6>Company Info</h6>
    <ul><li>Home</li><li>About Us</li><li>Capabilities</li><li>Job Seekers</li><li>Equipment</li><li>Hire Labour</li></ul>
  </div>
  <span class="divider" style="left:258px"></span>
  <div class="foot-col" style="left:282px;width:182px">
    <h6>Profile</h6>
    <p>A labour hire partner for underground coal, supplying trained crews, fair rosters and simple payroll to mines and contractors across New South Wales and Queensland. <span style="color:var(--ink)">Read</span></p>
  </div>
  <span class="divider" style="left:487px"></span>
  <div class="foot-col" style="left:511px">
    <h6>Newsletter</h6>
    <p style="font-size:7px">Enter Your Email</p>
    <div class="email-field"><span></span><b></b></div>
    <div class="socials" style="justify-content:flex-start;margin-top:10px"><span></span><span></span><span></span></div>
  </div>
  <div class="contact-card abs">
    <div class="contact-row"><svg width="12" height="10" viewBox="0 0 14 12"><path d="M1 4c0-2 3-3 6-3s6 1 6 3l-2 1-1-2H4L3 5z M3 6h8l1 5H2z" fill="#fff"/></svg><span>1800 555 014</span></div>
    <div class="contact-row"><svg width="12" height="10" viewBox="0 0 12 10"><rect x="0.5" y="0.5" width="11" height="9" fill="none" stroke="#fff"/><path d="M1 1l5 4 5-4" fill="none" stroke="#fff"/></svg><span>info@sfcrews.com</span></div>
    <div class="contact-row"><svg width="12" height="12" viewBox="0 0 12 12"><path d="M6 0a4 4 0 014 4c0 3-4 8-4 8S2 7 2 4a4 4 0 014-4z" fill="#fff"/></svg><span>New South Wales and<br>Queensland<br>P.O. Box 41207</span></div>
  </div>
</footer>
<div class="copyright abs">Copyright © 2014 Kestrel Ridge Pty Ltd</div>

</body>
</html>
```